Norvanta Assist Re-Design\ Add Hosting Content

We are redesigning our web site. We have already picked out the Cobalt SitePress Hosting theme. All content will come from our current website and go onto the new website. http://www.norvanta-assist.com . This website will interface with WHMCS billing software. I have attached old logos as well as icons for the hosting theme which is also attached.

Target Market(s)

Tech, Web, Hosting

Industry/Entity Type

Tech

Logo Text

Norvanta Assist, "The New IT Department"

```html
<!DOCTYPE html>
<html lang="en">
<head>
<meta charset="utf-8">
<title>Norvanta Assist</title>
<link href="https://fonts.googleapis.com/css2?family=Open+Sans:wght@400;600;700&family=Raleway:wght@300;400;600;700&display=swap" rel="stylesheet">
<style>
:root{
  --red:#d5121e;
  --dark:#1b1b1d;
  --darker:#121214;
  --navy:#283a8f;
  --text:#555;
  --muted:#8a8a8a;
  --light:#f3f3f3;
  --line:#dcdcdc;
  --white:#fff;
}
*{box-sizing:border-box;margin:0;padding:0}
html,body{width:1200px;height:3442px;overflow:hidden}
body{font-family:"Open Sans",Arial,sans-serif;color:var(--text);background:var(--white);position:relative}
.abs{position:absolute}

.topbar{left:0;top:0;width:1200px;height:46px;background:var(--red);color:var(--white);font-size:11px}
.topbar .contact{left:98px;top:15px;display:flex;gap:38px}
.topbar .contact span{display:flex;align-items:center;gap:8px}
.topbar .social{right:100px;top:13px;display:flex;gap:26px}
.topbar .social i{width:10px;height:10px;border-radius:50%;background:var(--white);display:block;margin-top:4px}

.header{left:0;top:46px;width:1200px;height:104px;background:var(--white)}
.brand{left:98px;top:25px;display:flex;align-items:center;gap:10px}
.brand .dot{width:46px;height:46px;border-radius:50%;background:var(--navy)}
.brand .name{font-family:"Raleway",sans-serif;font-weight:700;font-size:22px;color:var(--navy);line-height:1}
.brand .tag{font-size:11px;color:var(--red);margin-top:3px}
.brand .site{font-size:12px;color:var(--red);font-weight:700;letter-spacing:.5px}
.nav{left:474px;top:43px;display:flex;gap:44px;font-family:"Raleway",sans-serif;font-size:13px;text-transform:uppercase;color:#666}
.nav .active{color:var(--navy)}

.hero{left:0;top:150px;width:1200px;height:447px;background:linear-gradient(120deg,#2a2a2c 0%,#111 55%,#1e1e20 100%)}
.hero .kicker{left:98px;top:74px;font-family:"Raleway",sans-serif;font-size:25px;color:var(--white);font-weight:400}
.hero .title{left:98px;top:110px;font-family:"Raleway",sans-serif;font-size:27px;color:var(--white);font-weight:700}
.hero .title em{color:var(--red);font-style:normal}
.hero ul{left:98px;top:166px;list-style:none;color:#e5e5e5;font-size:13px}
.hero li{display:flex;align-items:center;gap:12px;height:31.5px}
.btn-red{background:var(--red);color:var(--white);font-family:"Raleway",sans-serif;font-weight:600;font-size:14px;display:flex;align-items:center;justify-content:center;text-transform:uppercase}
.hero .btn-red{left:98px;top:347px;width:167px;height:38px}
.hero .rack{left:612px;top:100px;width:425px;height:270px;border-radius:8px;background:linear-gradient(90deg,#4b4e5a,#9ba1b5 50%,#4a4c55)}
.hero .arrow{top:200px}

.promo{left:0;top:597px;width:1200px;height:103px;background:var(--red)}
.promo p{left:122px;top:17px;width:700px;font-family:"Raleway",sans-serif;font-size:22px;color:var(--white);line-height:34px}
.promo .btn-outline{left:920px;top:30px;width:163px;height:41px;border:2px solid var(--white);color:var(--white);font-family:"Raleway",sans-serif;font-size:15px;display:flex;align-items:center;justify-content:center}

.intro-title{left:0;top:758px;width:1200px;text-align:center;font-family:"Raleway",sans-serif;font-weight:700;font-size:17px;color:#222}
.intro-title em{font-style:normal;color:var(--red)}
.card{top:822px;width:312px;height:337px;background:var(--light);text-align:center}
.card .icon{width:110px;height:95px;margin:30px auto 0;border-radius:6px}
.card h3{margin-top:30px;font-family:"Raleway",sans-serif;font-weight:400;font-size:19px;color:#333;text-transform:uppercase}
.card p{margin:15px auto 0;width:250px;font-size:11.5px;line-height:20px;color:var(--muted)}
.btn-ghost{display:inline-flex;align-items:center;justify-content:center;width:118px;height:35px;border:1px solid #bbb;background:#f7f7f7;font-family:"Raleway",sans-serif;font-size:13px;color:#666;margin-top:24px}

.consult{left:0;top:1193px;width:1200px;height:512px;background:linear-gradient(160deg,#2a2a2c,#161618 60%,#242426);clip-path:polygon(0 8%,52% 0,52% 4%,100% 0,100% 92%,52% 100%,52% 94%,0 100%)}
.consult h2{left:0;top:140px;width:1200px;text-align:center;font-family:"Raleway",sans-serif;font-size:21px;color:var(--white);font-weight:400}
.consult h2 b{font-weight:700}
.consult .sub{left:0;top:182px;width:1200px;text-align:center;font-size:14px;color:#cfcfcf}
.field{height:38px;border:1px solid #777;background:rgba(255,255,255,.14);color:#ddd;font-size:12px;padding:11px 15px}
.consult .btn-red{left:492px;top:407px;width:216px;height:37px;font-size:13px}

.section-title{left:0;width:1200px;text-align:center;font-family:"Raleway",sans-serif;font-size:21px;color:#333;font-weight:400;text-transform:uppercase}
.section-title b{font-weight:700}
.section-title em{font-style:normal;color:var(--red);font-weight:700}
.section-sub{left:0;width:1200px;text-align:center;font-size:14px;color:var(--muted)}

.quote{top:1875px;width:482px;height:160px;background:var(--light);border:1px solid #e4e4e4;padding:22px 26px;font-size:11.5px;line-height:21px;color:var(--muted)}
.quote::after{content:"";position:absolute;left:40px;bottom:-14px;border:7px solid transparent;border-top-color:var(--light)}
.avatar{top:2062px;width:72px;height:72px;border-radius:50%;background:linear-gradient(#8a8a8a,#3a3a3a)}
.who{top:2080px;font-size:12.5px;color:#333;line-height:21px}
.who em{font-style:italic;color:var(--red)}
.who b{font-style:italic}

.news{left:0;top:2157px;width:1200px;height:517px;background:linear-gradient(170deg,#1e1e20,#2e2e30 50%,#17171a);clip-path:polygon(0 0,52% 12%,52% 5%,100% 18%,100% 100%,52% 88%,52% 95%,0 82%)}
.news h2{top:126px;color:var(--white)}
.news .section-sub{top:170px;color:#ccc}
.post{top:230px;width:312px;display:flex;gap:14px;color:#ccc}
.post .date{font-family:"Raleway",sans-serif;font-weight:700;color:var(--white);font-size:30px;line-height:30px;text-align:center}
.post .date span{display:block;color:var(--red);font-size:16px;line-height:20px}
.post h4{font-family:"Raleway",sans-serif;font-weight:400;font-size:18px;color:var(--white);margin-bottom:10px}
.post p{font-size:11.5px;line-height:20px}
.post a{color:var(--red);font-size:11.5px;text-decoration:none}

.service{width:262px;display:flex;gap:14px}
.service .ico{flex:none;width:42px;height:42px;border-radius:6px}
.service h5{font-family:"Raleway",sans-serif;font-weight:400;font-size:12px;color:var(--navy);text-transform:uppercase;margin-bottom:6px;white-space:nowrap}
.service p{font-size:11.5px;line-height:21px;color:var(--muted);width:190px}

.footer{left:0;top:3064px;width:1200px;height:328px;background:var(--dark);clip-path:polygon(0 0,52% 16%,52% 10%,100% 24%,100% 100%,0 100%)}
.footer h6{font-family:"Raleway",sans-serif;font-weight:700;font-size:13px;color:var(--white);text-transform:uppercase}
.footer .col{top:118px;font-size:11px;color:#aaa;line-height:22px}
.footer .row{display:flex;gap:12px;align-items:flex-start}
.footer .row i{width:9px;height:9px;background:var(--red);display:block;margin-top:6px;flex:none}
.footer .tweet{margin-bottom:14px;line-height:18px}
.footer .tweet small{display:block;color:var(--red)}
.footer .circles{display:flex;gap:9px;margin-top:22px}
.footer .circles i{width:20px;height:20px;border-radius:50%;background:#555;display:block}
.copy{left:0;top:3392px;width:1200px;height:50px;background:var(--red);color:var(--white);font-size:12px;display:flex;align-items:center;justify-content:center}
</style>
</head>
<body>

<div class="abs topbar">
  <div class="abs contact">
    <span><svg width="8" height="12" viewBox="0 0 8 12"><rect x="0.5" y="0.5" width="7" height="11" rx="1.5" fill="none" stroke="#fff"/></svg>Call Us Today! (555) 014-2277</span>
    <span><svg width="12" height="9" viewBox="0 0 12 9"><rect x="0.5" y="0.5" width="11" height="8" fill="none" stroke="#fff"/><path d="M.5 .5 6 5l5.5-4.5" fill="none" stroke="#fff"/></svg>Email: support@norvanta-assist.com</span>
  </div>
  <div class="abs social"><i></i><i></i><i></i><i></i></div>
</div>

<header class="abs header">
  <div class="abs brand">
    <div class="dot"></div>
    <div>
      <div class="name">Norvanta Assist</div>
      <div class="tag">"The New IT Department"</div>
      <div class="site">NORVANTA-ASSIST.COM</div>
    </div>
  </div>
  <nav class="abs nav">
    <span class="active">Home</span><span>Services</span><span>Business Users</span><span>Home Users</span><span>About Us</span><span>Contact</span>
  </nav>
</header>

<section class="abs hero">
  <div class="abs kicker">WE CAN PROVIDE</div>
  <div class="abs title">INDUSTRY <em>PROVEN EXPERTIES</em></div>
  <ul class="abs">
    <li><svg width="10" height="9"><path d="M1 5l3 3 5-7" stroke="#d5121e" stroke-width="2" fill="none"/></svg>Unlimited Disk Space,Bandwidth &amp; Email Address</li>
    <li><svg width="10" height="9"><path d="M1 5l3 3 5-7" stroke="#d5121e" stroke-width="2" fill="none"/></svg>FREE Domain Registration</li>
    <li><svg width="10" height="9"><path d="M1 5l3 3 5-7" stroke="#d5121e" stroke-width="2" fill="none"/></svg>FREE Security Suite</li>
    <li><svg width="10" height="9"><path d="M1 5l3 3 5-7" stroke="#d5121e" stroke-width="2" fill="none"/></svg>FREE Site-Building Tools</li>
    <li><svg width="10" height="9"><path d="M1 5l3 3 5-7" stroke="#d5121e" stroke-width="2" fill="none"/></svg>FREE Search Engine &amp; Marketing Credits</li>
  </ul>
  <div class="abs btn-red">Learn More</div>
  <div class="abs rack" role="img" aria-label="Row of server rack cabinets"></div>
  <svg class="abs arrow" style="left:22px" width="14" height="30"><path d="M12 2 2 15l10 13" stroke="#777" stroke-width="2" fill="none"/></svg>
  <svg class="abs arrow" style="right:22px" width="14" height="30"><path d="M2 2l10 13L2 28" stroke="#777" stroke-width="2" fill="none"/></svg>
</section>

<section class="abs promo">
  <p class="abs">Norvanta Assist now offers on-line ordering. Visit <b>NVA Shop</b> to find out more</p>
  <div class="abs btn-outline">GET STARTED</div>
</section>

<h2 class="abs intro-title">NORVANTA ASSIST IS THE IT SUPPORT SOLUTION TO YOUR <em>BUSINESS &amp; HOME</em> NEEDS!</h2>

<div class="abs card" style="left:98px">
  <div class="icon" role="img" aria-label="Desktop monitor icon" style="background:linear-gradient(#3b7fd1,#1d3f7a)"></div>
  <h3>$50 Flat Rate Repair</h3>
  <p>When it comes to business, IT is an absolute must. However, hiring your own IT employees isn't. NVA IT support department.</p>
  <span class="btn-ghost">LEARN MORE</span>
</div>
<div class="abs card" style="left:443px">
  <div class="icon" role="img" aria-label="Stack of backup drives icon" style="background:linear-gradient(#c9c9c9,#5c5c5c)"></div>
  <h3>Online Backup</h3>
  <p>When it comes to business, IT is an absolute must. However, hiring your own IT employees isn't. NVA IT support department.</p>
  <span class="btn-ghost">LEARN MORE</span>
</div>
<div class="abs card" style="left:788px">
  <div class="icon" role="img" aria-label="Envelope icon" style="background:linear-gradient(#f2f2f2,#c8c8c8)"></div>
  <h3>Email Solutions</h3>
  <p>When it comes to business, IT is an absolute must. However, hiring your own IT employees isn't. NVA IT support department.</p>
  <span class="btn-ghost">LEARN MORE</span>
</div>

<section class="abs consult" role="img" aria-label="Dark photo of a server room with a person standing">
  <h2 class="abs"><b>FREE</b> CONSULTATIONS</h2>
  <p class="abs sub">Receive a FREE Consultation Now! Norvanta Assist Has You Covered</p>
  <div class="abs field" style="left:98px;top:253px;width:310px">Enter Your Name</div>
  <div class="abs field" style="left:445px;top:253px;width:310px">Enter Your Email</div>
  <div class="abs field" style="left:792px;top:253px;width:308px">Enter Your Phone</div>
  <div class="abs field" style="left:98px;top:312px;width:1002px;height:60px">Enter Your Name</div>
  <div class="abs btn-red">Submit Now!</div>
</section>

<h2 class="abs section-title" style="top:1778px">
  <svg width="10" height="16" style="margin-right:18px"><path d="M8 1 2 8l6 7" stroke="#555" stroke-width="2" fill="none"/></svg>What Our <em>Clients Say</em><svg width="10" height="16" style="margin-left:18px"><path d="M2 1l6 7-6 7" stroke="#555" stroke-width="2" fill="none"/></svg>
</h2>
<p class="abs section-sub" style="top:1820px">When it comes to business, IT is an absolute must. However, hiring&nbsp; IT support department.</p>

<div class="abs quote" style="left:98px">“ After a competitive bid review, we contracted with Norvanta Assist to be our IT Department Network Administrator. NVA is a collaborative partner that has met our expectations. We trust our computers and / or network are in good hands with Norvanta Assist. We are spending less and have shortened our system down time.~ Ray K&amp;M Electric (Riverton, NE)</div>
<div class="abs quote" style="left:620px">“ After a competitive bid review, we contracted with Norvanta Assist to be our IT Department Network Administrator. NVA is a collaborative partner that has met our expectations. We trust our computers and / or network are in good hands with Norvanta Assist. We are spending less and have shortened our system down time.~ Ray K&amp;M Electric (Riverton, NE)</div>
<div class="abs avatar" style="left:100px" role="img" aria-label="Client portrait"></div>
<div class="abs who" style="left:190px">Name : <em>Dummy Name</em><br><b>Posted on 25 mArch 2015</b></div>
<div class="abs avatar" style="left:622px" role="img" aria-label="Client portrait"></div>
<div class="abs who" style="left:712px">Name : <em>Dummy Name</em><br><b>Posted on 25 march 2015</b></div>

<section class="abs news" role="img" aria-label="Dark city background photo">
  <h2 class="abs section-title">Recent <b>News</b></h2>
  <p class="abs section-sub">Norvanta Assist Is The IT Support Solution To Your Business &amp; Home Needs!</p>
  <div class="abs post" style="left:98px"><div class="date">25<span>MAY</span></div><div><h4>Innovations in Education</h4><p>When it comes to business, IT is an absolute must. However, hiring your own IT employees isn't. NVA IT support department.When it comes to employees isn't. NVA IT support Life department.</p><a>Read More</a></div></div>
  <div class="abs post" style="left:443px"><div class="date">25<span>MAY</span></div><div><h4>Innovations in Education</h4><p>When it comes to business, IT is an absolute must. However, hiring your own IT employees isn't. NVA IT support department.When it comes to employees isn't. NVA IT support Life department.</p><a>Read More</a></div></div>
  <div class="abs post" style="left:788px"><div class="date">25<span>MAY</span></div><div><h4>Innovations in Education</h4><p>When it comes to business, IT is an absolute must. However, hiring your own IT employees isn't. NVA IT support department.When it comes to employees isn't. NVA IT support Life department.</p><a>Read More</a></div></div>
</section>

<h2 class="abs section-title" style="top:2712px">Our <b>Services</b></h2>
<p class="abs section-sub" style="top:2750px">When it comes to business, IT is an absolute must. However, hiring&nbsp; IT support department.</p>

<div class="abs service" style="left:96px;top:2818px"><div class="ico" role="img" aria-label="Padlock icon" style="background:#d9a531"></div><div><h5>Data Backup &amp; Recovery</h5><p>When it comes to business, IT an absolute must. However, IT support department.</p></div></div>
<div class="abs service" style="left:355px;top:2818px"><div class="ico" role="img" aria-label="Monitor icon" style="background:#3e6fb3"></div><div><h5>Repair &amp; Diagnostics</h5><p>When it comes to business, IT an absolute must. However, IT support department.</p></div></div>
<div class="abs service" style="left:620px;top:2818px"><div class="ico" role="img" aria-label="Shield icon" style="background:#c9a24a"></div><div><h5>Virus &amp; Malware Protection</h5><p>When it comes to business, IT an absolute must. However, IT support department.</p></div></div>
<div class="abs service" style="left:883px;top:2818px"><div class="ico" role="img" aria-label="Tools icon" style="background:#b63a3a"></div><div><h5>Updates &amp; Installations</h5><p>When it comes to business, IT an absolute must. However, IT support department.</p></div></div>
<div class="abs service" style="left:96px;top:2950px"><div class="ico" role="img" aria-label="Database icon" style="background:#8d8d8d"></div><div><h5>Computer Networking</h5><p>When it comes to business, IT an absolute must. However, IT support department.</p></div></div>
<div class="abs service" style="left:355px;top:2950px"><div class="ico" role="img" aria-label="Mail icon" style="background:#e0b52e"></div><div><h5>Email Setup</h5><p>When it comes to business, IT an absolute must. However, IT support department.</p></div></div>
<div class="abs service" style="left:620px;top:2950px"><div class="ico" role="img" aria-label="Hard drive icon" style="background:#5a5a5a"></div><div><h5>System Troubleshooting</h5><p>When it comes to business, IT an absolute must. However, IT support department.</p></div></div>
<div class="abs service" style="left:883px;top:2950px"><div class="ico" role="img" aria-label="Computer tower icon" style="background:#b9b9b9"></div><div><h5>Optimizing Computer Speed</h5><p>When it comes to business, IT an absolute must. However, IT support department.</p></div></div>

<footer class="abs footer">
  <div class="abs col" style="left:103px;width:230px">
    <h6>Contact Us</h6>
    <div style="margin-top:18px">
      <div class="row"><i></i>(555) 014-2277(Phone)</div>
      <div class="row"><i></i>http://www.norvanta-assist.com (Fax)</div>
      <div class="row"><i></i>info@norvanta-assist.com</div>
      <div class="row"><i style="border-radius:50%"></i>2210 N. 88th Street, Ste 204<br>Riverton, Nebraska 68000</div>
    </div>
  </div>
  <div class="abs col" style="left:355px;width:250px">
    <h6>Social Feed</h6>
    <div style="margin-top:18px">
      <div class="tweet">@pixelmoor. Harbor site theme full responsive is coming soon...<small>4 days ago</small></div>
      <div class="tweet">@pixelmoor. Harbor site theme full responsive is coming soon...<small>4 days ago</small></div>
    </div>
  </div>
  <div class="abs col" style="left:670px;width:200px">
    <h6>Quick Links</h6>
    <div style="margin-top:14px">About Norvanta Assist<br>Our Partners<br>Terms &amp; Conditions<br>Privacy Policy<br>Certifications<br>Testimonials<br>Contact Us</div>
  </div>
  <div class="abs col" style="left:930px;width:180px">
    <h6>Follow Us</h6>
    <div style="margin-top:18px;line-height:18px">Lorem ipsum dolor sit amet, consectetur adipiscing elit. Nulla in purus nibh. Donec ornare.</div>
    <div class="circles"><i></i><i style="background:#fff"></i><i></i><i></i><i></i></div>
  </div>
</footer>

<div class="abs copy">© Copyright - 2015 Norvanta Assist, LLC. All Rights Reserved.</div>

</body>
</html>
```